Natural Light/Organic/Documentary Photography Business

I like a simple, approachable, feminine, earthy/organic feel. Earth/neutral tones, nothing too loud or obnoxious. I like the watercolor look. I don't want anything too trendy or something I'll get tired of after a couple months. As far as colors, I am much more a fan of cream/taupe/blue/green...not a fan of pink or purple at all.

Target Market(s)

Weddings & Families

Industry/Entity Type

Wedding Photography

Contact Information for Business Card

website, email, phone number

Font styles to use
Other font styles liked:
• Horizontes, Gotham

Colors

Designer to choose colors to be used in the design.

Requirements
Must have
• Website: www.mirelhatchway.com
• Phone: 418.629.5073
• Email: mirel@mirelhatchway.com
Nice to have
• I like the watercolor look but its not necessary. I like simple/earthy tones. Nothing too loud or distracting. Simple & feminine without being too girly. I like an approachable/soft feel.
• Instagram: www.instagram.com/mirelhatchwayphotography/
Should not have
• NO loud colors or design or pattern. I do not want a photo of a camera or lens or anything cheesy like that.

```html
<!DOCTYPE html>
<html lang="en">
<head>
<meta charset="utf-8">
<title>Mirel Hatchway Photography — Business Card</title>
<link href="https://fonts.googleapis.com/css2?family=Lato:wght@300;400&display=swap" rel="stylesheet">
<style>
  :root {
    --backdrop: #8c8c8c;
    --card-white: #ffffff;
    --card-mist: #efefef;
    --ink: #3f3a36;
    --taupe: #7a6e66;
    --rule: #8a827c;
    --sand: #efd9bd;
    --sage: #c9e3c4;
  }
  * { margin: 0; padding: 0; box-sizing: border-box; }
  html, body { width: 1200px; height: 1200px; overflow: hidden; }
  body {
    background: var(--backdrop);
    font-family: "Lato", sans-serif;
    position: relative;
  }
  .card {
    position: absolute;
    top: 310px;
    height: 594px;
    box-shadow: 3px 4px 6px rgba(0,0,0,0.35);
    overflow: hidden;
  }
  .card--front { left: 234px; width: 364px; background: var(--card-white); }
  .card--back { left: 628px; width: 368px; background: var(--card-mist); }

  .artwork {
    position: absolute;
    left: 0; width: 100%;
    background: linear-gradient(160deg, var(--sand) 0%, var(--sage) 100%);
  }
  .card--front .artwork { top: 0; height: 472px; }
  .card--back .artwork { bottom: 0; height: 128px; }

  .wordmark {
    position: absolute;
    left: 0; width: 100%;
    text-align: center;
    color: var(--taupe);
  }
  .wordmark__name {
    display: block;
    font-weight: 300;
    font-size: 40px;
    line-height: 44px;
    letter-spacing: 1px;
  }
  .wordmark__tag {
    display: block;
    font-weight: 300;
    font-size: 8px;
    letter-spacing: 5px;
    margin-top: 2px;
  }
  .card--front .wordmark { top: 494px; }
  .card--back .wordmark { top: 118px; }

  .rule {
    position: absolute;
    left: 112px; width: 150px;
    height: 1px;
    background: var(--rule);
  }
  .rule--top { top: 206px; }
  .rule--bottom { top: 335px; }

  .contact {
    position: absolute;
    top: 228px; left: 0; width: 100%;
    text-align: center;
    color: var(--ink);
    font-size: 20px;
    line-height: 24.5px;
    list-style: none;
  }
  .social {
    position: absolute;
    top: 366px; left: 0; width: 100%;
    text-align: center;
    color: var(--ink);
    font-size: 17px;
  }
</style>
</head>
<body>
  <section class="card card--front">
    <div class="artwork" role="img" aria-label="Abstract watercolour artwork area"></div>
    <div class="wordmark">
      <span class="wordmark__name">Mirel Hatchway</span>
      <span class="wordmark__tag">PHOTOGRAPHY</span>
    </div>
  </section>

  <section class="card card--back">
    <div class="wordmark">
      <span class="wordmark__name">Mirel Hatchway</span>
      <span class="wordmark__tag">PHOTOGRAPHY</span>
    </div>
    <div class="rule rule--top"></div>
    <ul class="contact">
      <li>418.629.5073</li>
      <li>mirel@mirelhatchway.com</li>
      <li>www.mirelhatchway.com</li>
    </ul>
    <div class="rule rule--bottom"></div>
    <p class="social">instagram.com/mirelhatchwayphotography</p>
    <div class="artwork" role="img" aria-label="Abstract watercolour artwork area"></div>
  </section>
</body>
</html>
```